Up to the Challenge - PPT Template with Splash Slide

We are looking for a PPT template that has 4 slides.
1. Splash slide (Creative, fun, no content, a visual representation of the theme)
2. Section header slide
3. Content Slide
4. Content Slide, another design option
The theme is 'UP to the Challenge'. The design should reflect this theme.
The colors should be in Purple (#864B99), Blue (#0A80C2), and Green (#52B054).

```html
<!DOCTYPE html>
<html lang="en">
<head>
<meta charset="utf-8">
<title>Up to the Challenge – Slide Template</title>
<link href="https://fonts.googleapis.com/css2?family=Poppins:wght@400;500;600;700&display=swap" rel="stylesheet">
<style>
  :root{
    --purple:#864B99;
    --blue:#0A80C2;
    --green:#52B054;
    --heading-blue:#2F6DB5;
    --ink:#333333;
    --body:#3a3a3a;
    --canvas:#F2F2F2;
    --white:#FFFFFF;
  }
  *{box-sizing:border-box;margin:0;padding:0;}
  html,body{width:1105px;height:1200px;overflow:hidden;background:var(--canvas);font-family:'Poppins',sans-serif;}
  .board{position:relative;width:1105px;height:1200px;}
  .slide{position:absolute;width:481px;height:270px;background:var(--white);overflow:hidden;}
  .col-left{left:48px;}
  .col-right{left:577px;}
  .row-1{top:27px;} .row-2{top:311px;} .row-3{top:597px;} .row-4{top:882px;}

  .title-bar{position:absolute;left:6px;right:0;top:12px;height:33px;background:var(--green);border-radius:17px 0 0 17px;
    color:var(--white);font-weight:700;font-size:22px;line-height:33px;padding-left:14px;letter-spacing:.3px;}
  .page-no{position:absolute;right:7px;bottom:6px;width:13px;height:13px;border-radius:50%;background:var(--blue);
    color:var(--white);font-size:6px;font-weight:600;line-height:13px;text-align:center;}
  .page-no.light{background:var(--white);color:var(--ink);}

  .photo{position:absolute;inset:0;}
  .photo-sky{background:linear-gradient(180deg,#c9d6e6 0%,#e4e8ee 55%,#d9dde3 80%,#8e6b4e 100%);}
  .photo-team{background:radial-gradient(ellipse at 55% 50%,#2f8a86 0%,#1f6a5a 45%,#154a3d 100%);}

  /* agenda */
  .agenda-item{position:absolute;width:182px;}
  .tick{position:absolute;left:-36px;top:-2px;width:25px;height:25px;border-radius:50%;background:var(--purple);}
  .tick svg{position:absolute;left:6.5px;top:7.5px;}
  .agenda-item h3{font-size:12px;font-weight:600;color:var(--heading-blue);line-height:16px;white-space:nowrap;}
  .agenda-item p{font-size:9.3px;color:var(--body);line-height:12.6px;margin-top:2px;}

  /* text blocks */
  .copy p{font-size:7.8px;line-height:13.5px;color:var(--body);text-align:justify;margin-bottom:5.5px;}
  .copy.wide p{font-size:8px;line-height:13.3px;margin-bottom:6.5px;}

  .image-title{position:absolute;left:13px;top:31px;font-size:22px;font-weight:700;color:var(--ink);line-height:20px;width:220px;}
  .image-blob{position:absolute;right:0;top:0;}

  .col-icon{position:absolute;width:38px;height:38px;border-radius:50%;border:1px solid var(--purple);}
  .col-icon svg{position:absolute;left:9px;top:9px;}
  .col-heading{position:absolute;font-size:14.5px;font-weight:600;color:var(--heading-blue);}

  .card{position:absolute;top:67px;width:144px;height:172px;background:linear-gradient(160deg,#8a4c9b 0%,#4d63b4 50%,#0a80c2 100%);
    text-align:center;color:var(--white);}
  .portrait{position:absolute;left:42px;top:16px;width:60px;height:60px;border-radius:50%;border:1.5px solid var(--white);
    background:linear-gradient(180deg,#d7dbe0 0%,#8d96a3 60%,#3a4150 100%);}
  .card h3{position:absolute;top:86px;left:0;right:0;font-size:14px;font-weight:600;}
  .card p{position:absolute;top:109px;left:8px;right:8px;font-size:7.9px;line-height:13.2px;}

  .break-title{position:absolute;left:0;right:0;top:120px;text-align:center;color:var(--white);font-size:22px;font-weight:700;}

  .thanks{background:radial-gradient(ellipse at 50% 50%,#5f8a6c 0%,#6f7a80 45%,#84559a 100%);color:var(--white);text-align:center;}
  .thanks .dash{position:absolute;left:225px;top:64px;width:30px;height:2.5px;background:var(--white);}
  .thanks h2{position:absolute;left:0;right:0;top:78px;font-size:23px;font-weight:700;}
  .thanks p{position:absolute;left:48px;right:48px;top:118px;font-size:10.4px;line-height:17.3px;}
  .social{position:absolute;top:177px;width:22px;height:22px;border-radius:50%;border:1px solid var(--white);
    font-size:5px;font-weight:500;line-height:20px;}
</style>
</head>
<body>
<div class="board">

  <!-- Splash -->
  <section class="slide col-left row-1">
    <div class="photo photo-sky" role="img" aria-label="Businessman carrying an elephant on his back while walking a tightrope between two cliffs against a cloudy sky"></div>
  </section>

  <!-- Agenda -->
  <section class="slide col-left row-2">
    <div class="title-bar">Agenda</div>
    <div class="agenda-item" style="left:42px;top:67px;"><span class="tick"><svg width="12" height="10" viewBox="0 0 12 10"><path d="M1 5l3.5 3.5L11 1.5" fill="none" stroke="#fff" stroke-width="1.8"/></svg></span><h3>Excepteur sint occaecat</h3><p>Sed ut perspiciatis unde omnis iste natus error sit voluptate</p></div>
    <div class="agenda-item" style="left:287px;top:67px;"><span class="tick"><svg width="12" height="10" viewBox="0 0 12 10"><path d="M1 5l3.5 3.5L11 1.5" fill="none" stroke="#fff" stroke-width="1.8"/></svg></span><h3>Excepteur sint occaecat</h3><p>Sed ut perspiciatis unde omnis iste natus error sit voluptate</p></div>
    <div class="agenda-item" style="left:42px;top:125px;"><span class="tick"><svg width="12" height="10" viewBox="0 0 12 10"><path d="M1 5l3.5 3.5L11 1.5" fill="none" stroke="#fff" stroke-width="1.8"/></svg></span><h3>Excepteur sint occaecat</h3><p>Sed ut perspiciatis unde omnis iste natus error sit voluptate</p></div>
    <div class="agenda-item" style="left:287px;top:125px;"><span class="tick"><svg width="12" height="10" viewBox="0 0 12 10"><path d="M1 5l3.5 3.5L11 1.5" fill="none" stroke="#fff" stroke-width="1.8"/></svg></span><h3>Excepteur sint occaecat</h3><p>Sed ut perspiciatis unde omnis iste natus error sit voluptate</p></div>
    <div class="agenda-item" style="left:42px;top:189px;"><span class="tick"><svg width="12" height="10" viewBox="0 0 12 10"><path d="M1 5l3.5 3.5L11 1.5" fill="none" stroke="#fff" stroke-width="1.8"/></svg></span><h3>Excepteur sint occaecat</h3><p>Sed ut perspiciatis unde omnis iste natus error sit voluptate</p></div>
    <div class="agenda-item" style="left:287px;top:189px;"><span class="tick"><svg width="12" height="10" viewBox="0 0 12 10"><path d="M1 5l3.5 3.5L11 1.5" fill="none" stroke="#fff" stroke-width="1.8"/></svg></span><h3>Excepteur sint occaecat</h3><p>Sed ut perspiciatis unde omnis iste natus error sit voluptate</p></div>
    <span class="page-no">2</span>
  </section>

  <!-- Break -->
  <section class="slide col-left row-3">
    <div class="photo photo-team" role="img" aria-label="Hands of a team fitting four puzzle pieces together on a wooden table, tinted green"></div>
    <h2 class="break-title">Break Slide Goes Here</h2>
    <span class="page-no light">3</span>
  </section>

  <!-- Content -->
  <section class="slide col-left row-4">
    <div class="title-bar">Content Slide</div>
    <div class="copy wide" style="position:absolute;left:15px;top:57px;width:455px;">
      <p>Sed ut perspiciatis unde omnis iste natus error sit voluptatem accusantium doloremque laudantium, totam rem aperiam, eaque ipsa quae ab illo inventore veritatis et quasi architecto beatae vitae dicta sunt explicaboemo enim ipsam voluptatem quia voluptas sit aspernatur aut odit aut fugit, sed quia consequuntur magni dolores eos qui ratione voluptatem sequi nesciunt. Neque porro quisquam est, qui dolorem ipsum quia dolor sit amet, consectetur, adipisci velit, sed quia non numquam eius modi tempora incidunt ut.</p>
      <p>Labore et dolore magnam aliquam quaerat voluptatem. Ut enim ad minima veniam, quis nostrum exercitationem ullam corporis suscipit laboriosam, nisi ut aliquid ex ea commodi consequatur? Quis autem vel eum iure reprehenderit qui in ea voluptate velit esse quam nihil molestiae consequatur, vel illum qui dolorem eum fugiat quo voluptas nulla pariatur.</p>
      <p>Sed ut perspiciatis unde omnis iste natus error sit voluptatem accusantium doloremque laudantium, totam rem aperiam, eaque ipsa quae ab illo inventore veritatis et quasi architecto beatae vitae dicta sunt explicaboemo enim ipsam voluptatem quia voluptas sit aspernatur aut odit aut fugit, sed quia consequuntur magni dolores eos qui ratione voluptatem sequi nesciunt. Neque porro quisquam est</p>
    </div>
    <span class="page-no">4</span>
  </section>

  <!-- Content with image -->
  <section class="slide col-right row-1">
    <h2 class="image-title">Content Slide with Image</h2>
    <div class="copy" style="position:absolute;left:13px;top:88px;width:210px;">
      <p>Sed ut perspiciatis unde omnis iste natus error sit voluptatem accusantium doloremque laudantium, totam rem aperiam, eaque ipsa quae.</p>
      <p>Veritatis et quasi architecto beatae vitae dicta sunt explicaboemo enim ipsam voluptatem quia voluptas sit aspernatur aut odit aut fugit, sed quia consequ untur magni dolores eos.</p>
      <p>Neque porro quisquam est, qui dolorem ipsum quia dolor sit amet, consectetur, adipisci velit, sed quia non numquam eius modi tempora incidunt ut.</p>
    </div>
    <svg class="image-blob" width="247" height="236" viewBox="0 0 247 236" role="img" aria-label="Man pushing a huge boulder up a rocky hill at sunset">
      <defs>
        <radialGradient id="sunset" cx="0.85" cy="0.4" r="0.9">
          <stop offset="0" stop-color="#ffd27a"/>
          <stop offset="0.3" stop-color="#e08a2e"/>
          <stop offset="0.7" stop-color="#7a4420"/>
          <stop offset="1" stop-color="#2e2119"/>
        </radialGradient>
      </defs>
      <path d="M38 0H247V236C205 230 178 170 132 190C80 212 8 200 1 120C-4 60 14 18 38 0Z" fill="url(#sunset)"/>
    </svg>
    <span class="page-no">5</span>
  </section>

  <!-- Two column -->
  <section class="slide col-right row-2">
    <div class="title-bar">Two Coloum Content</div>
    <span class="col-icon" style="left:5px;top:63px;"><svg width="20" height="20" viewBox="0 0 20 20" fill="none" stroke="#444" stroke-width="1.2"><circle cx="13" cy="6" r="3.5"/><path d="M2 18h16M4 18v-5h3v5M9 18v-8h3v8"/></svg></span>
    <span class="col-heading" style="left:53px;top:72px;">Excepteur sint occaecat</span>
    <span class="col-icon" style="left:249px;top:63px;"><svg width="20" height="20" viewBox="0 0 20 20" fill="none" stroke="#444" stroke-width="1.2"><rect x="2" y="2" width="7" height="7" rx="1"/><rect x="11" y="11" width="7" height="7" rx="1"/><path d="M9 5.5h5v5"/></svg></span>
    <span class="col-heading" style="left:297px;top:72px;">Excepteur sint occaecat</span>
    <div class="copy" style="position:absolute;left:14px;top:109px;width:209px;">
      <p>Sed ut perspiciatis unde omnis iste natus error sit voluptatem accusantium doloremque laudantium, totam rem aperiam, eaque ipsa quae.</p>
      <p>Veritatis et quasi architecto beatae vitae dicta sunt explicaboemo enim ipsam voluptatem quia voluptas sit aspernatur aut odit aut fugit, sed quia consequ untur magni dolores eos.</p>
      <p>Neque porro quisquam est, qui dolorem ipsum quia dolor sit amet, consectetur, adipisci velit, sed quia non numquam eius modi tempora incidunt ut.</p>
    </div>
    <div class="copy" style="position:absolute;left:258px;top:109px;width:209px;">
      <p>Sed ut perspiciatis unde omnis iste natus error sit voluptatem accusantium doloremque laudantium, totam rem aperiam, eaque ipsa quae.</p>
      <p>Veritatis et quasi architecto beatae vitae dicta sunt explicaboemo enim ipsam voluptatem quia voluptas sit aspernatur aut odit aut fugit, sed quia consequ untur magni dolores eos.</p>
      <p>Neque porro quisquam est, qui dolorem ipsum quia dolor sit amet, consectetur, adipisci velit, sed quia non numquam eius modi tempora incidunt ut.</p>
    </div>
    <span class="page-no">6</span>
  </section>

  <!-- Three column -->
  <section class="slide col-right row-3">
    <div class="title-bar">Three Coloum Content</div>
    <div class="card" style="left:16px;"><span class="portrait" role="img" aria-label="Portrait of a smiling businessman in an office"></span><h3>Excepteur sint</h3><p>Sed ut perspiciatis unde omnis iste natus error sit voluptatem accusantium doloremque laudantiumotam</p></div>
    <div class="card" style="left:169px;"><span class="portrait" role="img" aria-label="Portrait of a smiling businesswoman holding a tablet"></span><h3>Excepteur sint</h3><p>Sed ut perspiciatis unde omnis iste natus error sit voluptatem accusantium doloremque laudantiumotam</p></div>
    <div class="card" style="left:323px;"><span class="portrait" role="img" aria-label="Portrait of a bearded businessman in a dark suit"></span><h3>Excepteur sint</h3><p>Sed ut perspiciatis unde omnis iste natus error sit voluptatem accusantium doloremque laudantiumotam</p></div>
    <span class="page-no">7</span>
  </section>

  <!-- Thank you -->
  <section class="slide col-right row-4 thanks">
    <span class="dash"></span>
    <h2>Thank You</h2>
    <p>Veritatis et quasi architecto beatae vitae dicta sunt explicaboemo enim ipsam voluptatem quia voluptas sit aspernatur aut odit aut fugit, sed quia consequuntur magni dolores eos.</p>
    <span class="social" style="left:191px;">Kivo</span>
    <span class="social" style="left:229px;">Nural</span>
    <span class="social" style="left:269px;">Pixa</span>
  </section>

</div>
</body>
</html>
```